Letterhead, stationery and email signature for construction business

I need the letterhead, stationery and email signature designs for a construction business. I want them to have a corporate feel to them.

I've attached the logo for reference.

```html
<!DOCTYPE html>
<html lang="en">
<head>
<meta charset="utf-8">
<title>Norvale Builds – Stationery Set</title>
<link rel="stylesheet" href="https://fonts.googleapis.com/css2?family=Montserrat:wght@400;500;600;700;800&display=swap">
<style>
  :root {
    --brand-blue: #234a9c;
    --brand-dark: #44424f;
    --paper: #f2f2f2;
    --backdrop: #e6e6e8;
    --ink: #2b2b33;
    --line-light: #f0f0f0;
  }
  * { margin: 0; padding: 0; box-sizing: border-box; }
  html, body { width: 1200px; height: 792px; overflow: hidden; }
  body {
    background: var(--backdrop);
    font-family: "Montserrat", Arial, sans-serif;
    position: relative;
    color: var(--ink);
  }
  .piece { position: absolute; }

  /* Brand name set as type */
  .brand-name {
    font-weight: 700;
    color: var(--brand-blue);
    letter-spacing: 0.02em;
    line-height: 1;
    white-space: nowrap;
  }
  .brand-lockup { display: flex; align-items: center; gap: 6px; }
  .brand-square { background: var(--brand-blue); flex: none; }

  /* Business card – front */
  .card-front {
    left: 166px; top: 72px; width: 158px; height: 90px;
    background: var(--brand-blue);
    display: flex; align-items: center; justify-content: center;
  }
  .card-front .brand-name { color: #fff; font-size: 9px; }

  /* Business card – back */
  .card-back {
    left: 166px; top: 182px; width: 158px; height: 90px;
    background: var(--paper); overflow: hidden;
  }
  .card-back .accent-block {
    position: absolute; right: 0; top: 0; width: 46px; height: 90px;
    background: var(--brand-blue);
  }
  .card-back .holder-name {
    position: absolute; left: 10px; top: 51px;
    font-size: 8.5px; font-weight: 700; letter-spacing: 0.12em; color: var(--brand-blue);
  }
  .card-back .holder-tag {
    position: absolute; left: 10px; top: 61px;
    font-size: 3.2px; letter-spacing: 0.4em; color: #777;
  }
  .card-back .holder-details {
    position: absolute; left: 10px; top: 66px;
    font-size: 3.3px; line-height: 5px; color: #555;
  }

  /* Letterhead */
  .letterhead {
    left: 372px; top: 104px; width: 295px; height: 416px;
    background: var(--paper);
  }
  .letterhead .brand-lockup { position: absolute; left: 19px; top: 40px; }
  .letterhead .brand-square { width: 14px; height: 14px; }
  .letterhead .brand-name { font-size: 10px; }
  .contact-list {
    position: absolute; left: 155px; top: 38px; width: 121px;
    list-style: none;
  }
  .contact-list li {
    display: flex; gap: 6px; align-items: flex-start;
    font-size: 4.3px; line-height: 7.8px; font-weight: 600; color: var(--brand-blue);
    margin-bottom: 2.5px; text-align: justify;
  }
  .contact-list svg { width: 7px; height: 7px; flex: none; margin-top: 0.4px; }
  .letter-body {
    position: absolute; left: 19px; top: 141px; width: 257px;
    font-size: 4.3px; line-height: 6.9px; font-weight: 600; color: var(--ink);
    text-align: justify;
  }
  .letter-body p { margin-bottom: 11px; }
  .letter-body p.tight { margin-bottom: 0; }
  .signature-area {
    position: absolute; left: 15px; top: 328px; width: 46px; height: 30px;
    background: linear-gradient(135deg, #e6e6e6, #dcdcde);
  }
  .signer {
    position: absolute; left: 19px; top: 363px;
    font-size: 4.8px; line-height: 7px; font-weight: 600; color: var(--ink);
  }
  .letterhead .foot-band {
    position: absolute; left: 0; bottom: 0; width: 100%; height: 8px;
    background: var(--brand-blue);
  }

  /* Envelope */
  .envelope {
    left: 337px; top: 550px; width: 330px; height: 164px;
    background: var(--paper); overflow: hidden;
  }
  .envelope .flap { position: absolute; left: 0; top: 0; width: 330px; height: 42px; }
  .envelope .brand-lockup { position: absolute; left: 117px; top: 73px; }
  .envelope .brand-square { width: 12px; height: 12px; }
  .envelope .brand-name { font-size: 10px; }

  /* Folders */
  .folder-small {
    left: 720px; top: 72px; width: 330px; height: 164px;
    background: var(--brand-blue); overflow: hidden;
  }
  .folder-large {
    left: 720px; top: 253px; width: 332px; height: 439px;
    background: var(--brand-blue); overflow: hidden; border-radius: 0 3px 3px 0;
  }
  .folder-panel { position: absolute; left: 0; top: 0; height: 100%; background: var(--brand-dark); }
  .folder-small .folder-panel { width: 190px; }
  .folder-large .folder-panel { width: 190px; }
  .folder-rule { position: absolute; top: 0; height: 100%; width: 13px; background: var(--line-light); }
  .folder-small .folder-rule { left: 190px; }
  .folder-large .folder-rule { left: 190px; }
  .folder-mark { position: absolute; color: #fff; font-size: 11px; }
  .folder-small .folder-mark { left: 218px; top: 74px; }
  .folder-large .folder-mark { left: 218px; top: 212px; }
</style>
</head>
<body>

  <!-- Business card front -->
  <section class="piece card-front" aria-label="Business card front">
    <span class="brand-name">NORVALE BUILDS</span>
  </section>

  <!-- Business card back -->
  <section class="piece card-back" aria-label="Business card back">
    <div class="accent-block"></div>
    <p class="holder-name">YOUR NAME</p>
    <p class="holder-tag">YOUR TAG LINE</p>
    <p class="holder-details">14 Harbor Lane, Portfield, 20410<br>www.norvalebuilds.example<br>info@norvalebuilds.example</p>
  </section>

  <!-- Letterhead -->
  <section class="piece letterhead" aria-label="Letterhead">
    <div class="brand-lockup">
      <span class="brand-square"></span>
      <span class="brand-name">NORVALE BUILDS</span>
    </div>

    <ul class="contact-list">
      <li>
        <svg viewBox="0 0 10 10" aria-hidden="true"><path d="M5 0.6a3 3 0 0 1 3 3c0 2.2-3 5.8-3 5.8S2 5.8 2 3.6a3 3 0 0 1 3-3z" fill="none" stroke="#234a9c" stroke-width="1.1"/><circle cx="5" cy="3.6" r="1" fill="#234a9c"/></svg>
        <span>Lorem ipsum dolor sit amet, consectetuer adipiscing elit, sed diam nonummy nibh euismod tincidunt ut laoreet dolore magna</span>
      </li>
      <li>
        <svg viewBox="0 0 10 10" aria-hidden="true"><circle cx="5" cy="5" r="4" fill="#234a9c"/></svg>
        <span>Lorem ipsum dolor sit amet, consectetuer</span>
      </li>
      <li>
        <svg viewBox="0 0 10 10" aria-hidden="true"><circle cx="5" cy="5" r="4" fill="none" stroke="#234a9c" stroke-width="1"/><ellipse cx="5" cy="5" rx="1.8" ry="4" fill="none" stroke="#234a9c" stroke-width="0.8"/><path d="M1 5h8" stroke="#234a9c" stroke-width="0.8"/></svg>
        <span>Lorem ipsum dolor sit amet, consectetuer</span>
      </li>
      <li>
        <svg viewBox="0 0 10 10" aria-hidden="true"><rect x="1" y="2.2" width="8" height="5.6" fill="#234a9c"/><path d="M1 2.4l4 3 4-3" fill="none" stroke="#f2f2f2" stroke-width="0.8"/></svg>
        <span>Lorem ipsum dolor sit amet, consectetuer</span>
      </li>
      <li>
        <svg viewBox="0 0 10 10" aria-hidden="true"><path d="M2.2 1.2l1.6-.2 1 2.3-1 .9a5.5 5.5 0 0 0 2.2 2.2l.9-1 2.3 1-.2 1.6c-.2.6-.8.9-1.4.8C4.5 8.4 1.6 5.5 1.4 2.6c-.1-.6.2-1.2.8-1.4z" fill="#234a9c"/></svg>
        <span>0840-5512-300</span>
      </li>
    </ul>

    <div class="letter-body">
      <p class="tight">Lorem ipsum dolor sit amet, consectetuer adipiscing elit, sed diam nonummy nibh euismod tincidunt ut laoreet dolore magna aliquam erat volutpat. Ut wisi enim ad minim veniam, quis nostrud exercitation ullamcorper suscipit lobortis nisl ut aliquip ex ea commodo consequat. Duis autem vel eum iriure dolor in hendrerit in vulputate velit esse molestie consequat, vel illum dolore eu feugiat nulla facilisis at vero eros et accumsan et iusto odio dignissim qui blandit praesent luptatum zzril delenit augue duis dolore te feugait nulla facilisi.</p>
      <p>Lorem ipsum dolor sit amet, cons ectetuer adipiscing elit, sed diam nonummy nibh euismod tincidunt ut laoreet dolore magna aliquam erat volutpat. Ut wisi enim ad minim veniam, quis nostrud exercitation ullamcorper suscipit lobortis nisl ut aliquip ex ea commodo consequat.</p>
      <p>Lorem ipsum dolor sit amet, consectetuer adipiscing elit, sed diam nonummy nibh euismod tincidunt ut laoreet dolore magna aliquam erat volutpat. Ut wisi enim ad minim veniam, quis nostrud exercitation ullamcorper suscipit lobortis nisl ut aliquip ex ea commodo consequat. Duis autem vel eum iriure dolor in hendrerit in vulputate velit esse molestie consequat, vel illum dolore eu feugiat nulla facilisis at vero eros et accumsan et iusto odio dignissim qui blandit praesent luptatum zzril delenit augue duis dolore te feugait nulla facilisi.</p>
      <p>Lorem ipsum dolor sit amet, consectetuer adipiscing elit, sed diam nonummy nibh euismod tincidunt ut laoreet dolore magna aliquam erat volutpat. Ut wisi enim ad minim veniam, quis nostrud exercitation ullamcorper suscipit lobortis nisl ut aliquip ex ea commodo consequat. Duis autem vel eum iriure dolor in hendrerit in vulputate velit esse molestie consequat, vel illum dolore eu feugiat nulla facilisis at vero eros et</p>
    </div>

    <div class="signature-area" role="img" aria-label="Handwritten signature"></div>
    <p class="signer">Your Name<br>Position</p>
    <div class="foot-band"></div>
  </section>

  <!-- Envelope -->
  <section class="piece envelope" aria-label="Envelope">
    <svg class="flap" viewBox="0 0 330 42" aria-hidden="true">
      <path d="M0 0h330l-3 30q-2 12-14 12H19Q7 42 5 30z" fill="#234a9c"/>
    </svg>
    <div class="brand-lockup">
      <span class="brand-square"></span>
      <span class="brand-name">NORVALE BUILDS</span>
    </div>
  </section>

  <!-- Presentation folder, closed -->
  <section class="piece folder-small" aria-label="Folder back">
    <div class="folder-panel"></div>
    <div class="folder-rule"></div>
    <span class="brand-name folder-mark">NORVALE BUILDS</span>
  </section>

  <!-- Presentation folder, front -->
  <section class="piece folder-large" aria-label="Folder front">
    <div class="folder-panel"></div>
    <div class="folder-rule"></div>
    <span class="brand-name folder-mark">NORVALE BUILDS</span>
  </section>

</body>
</html>
```